Business card for Sports Apparel business

DOUBLE SIDED DESIGN
We need business cards for a new sports apparel business. We are developing a protective headband for soccer initially.
Torvalle is focused on designing and developing head protection products to reduce the likelihood of concussion when playing sports. Exploring and understanding medical insights, material science research, current and former players experiences and governing bodies guidelines has allowed Torvalle to develop the safety, style, form and function requirements of a suitable product to bring to market.
Target Market(s)
Mums buying kits for the sons and daughters. Amateur footballers.
Industry/Entity Type
Sporting Good
Contact Information for Business Card
Martin Ashworth - CEO
Mobile: +44 7431589027
Email: martin@torvalle.co.uk
Tel: 0208 5519372
Helena Pargeter - COO
Mob: +44 7385 640117
Email: helena@torvalle.co.uk
Tel: 0208 5519372
Duncan Farrow - CCO
Mob: +44 7564 293081
Email: duncan@torvalle.co.uk
Tel: 0208 5519372
Look and feel
Each slider illustrates characteristics of the customer's brand and the style your logo design should communicate.

```html
<!DOCTYPE html>
<html lang="en">
<head>
<meta charset="utf-8">
<title>Torvalle Business Card</title>
<link href="https://fonts.googleapis.com/css2?family=Barlow+Semi+Condensed:wght@500&family=Montserrat:wght@400;600&display=swap" rel="stylesheet">
<style>
  :root {
    --backdrop: #1e1e1e;
    --card-grey: #666666;
    --text-light: #ffffff;
    --accent-blue: #1f5c99;
    --shadow: rgba(0, 0, 0, 0.55);
  }
  html, body {
    margin: 0;
    padding: 0;
    width: 1200px;
    height: 900px;
    overflow: hidden;
    background: var(--backdrop);
  }
  .canvas {
    position: relative;
    width: 1200px;
    height: 900px;
  }
  .card {
    position: absolute;
    left: 340px;
    width: 520px;
    height: 300px;
    background: var(--card-grey);
    box-shadow: 0 12px 30px var(--shadow);
    overflow: hidden;
  }
  .card-front { top: 110px; }
  .card-back { top: 470px; }

  .brand-name {
    position: absolute;
    inset: 0;
    display: flex;
    align-items: center;
    justify-content: center;
    font-family: "Montserrat", sans-serif;
    font-weight: 600;
    font-size: 46px;
    letter-spacing: 3px;
    color: var(--text-light);
    text-transform: uppercase;
  }

  .identity {
    position: absolute;
    right: 272px;
    top: 112px;
    text-align: right;
    color: var(--text-light);
  }
  .person-name {
    font-family: "Barlow Semi Condensed", sans-serif;
    font-weight: 500;
    font-size: 24px;
    text-transform: uppercase;
    line-height: 1.1;
  }
  .person-role {
    font-family: "Montserrat", sans-serif;
    font-size: 15px;
    line-height: 1.3;
    padding-right: 8px;
  }
  .divider {
    position: absolute;
    left: 264px;
    top: 108px;
    width: 1.5px;
    height: 70px;
    background: var(--text-light);
  }
  .contacts {
    position: absolute;
    left: 280px;
    top: 112px;
    margin: 0;
    padding: 0;
    list-style: none;
    font-family: "Montserrat", sans-serif;
    font-size: 14px;
    color: var(--text-light);
  }
  .contacts li {
    display: flex;
    align-items: center;
    gap: 9px;
    height: 21px;
  }
  .contacts svg {
    width: 13px;
    height: 13px;
    flex: none;
  }
  .edge-strip {
    position: absolute;
    left: 0;
    right: 0;
    bottom: 0;
    height: 5px;
    background: var(--accent-blue);
  }
</style>
</head>
<body>
<main class="canvas">
  <section class="card card-front" aria-label="Card front">
    <div class="brand-name">Torvalle</div>
  </section>

  <section class="card card-back" aria-label="Card back">
    <div class="identity">
      <div class="person-name">Martin Ashworth</div>
      <div class="person-role">CEO</div>
    </div>
    <div class="divider"></div>
    <ul class="contacts">
      <li>
        <svg viewBox="0 0 14 14" fill="none" stroke="#fff" stroke-width="1.2"><rect x="3.5" y="1" width="7" height="12" rx="1.2"/><line x1="6" y1="11" x2="8" y2="11"/></svg>
        0208 5519372
      </li>
      <li>
        <svg viewBox="0 0 14 14" fill="none" stroke="#fff" stroke-width="1.2"><path d="M3 1.5l2 2.5-1.2 1.5c.8 1.8 2.3 3.3 4 4L9.5 8l2.5 2-1 2.5C6 12.5 1.5 8 1.5 2.5z"/><path d="M8.5 2a4 4 0 0 1 3.5 3.5M8.5 4a2 2 0 0 1 1.5 1.5"/></svg>
        +44 7431589027
      </li>
      <li>
        <svg viewBox="0 0 14 14" fill="none" stroke="#fff" stroke-width="1.2"><rect x="1" y="3" width="12" height="8.5"/><path d="M1 3l6 5 6-5"/></svg>
        martin@torvalle.co.uk
      </li>
    </ul>
    <div class="edge-strip"></div>
  </section>
</main>
</body>
</html>
```